Building company buisness cards

We are looking for a sharp modern new look for our business cards.We are a New Zealand based company that specialises in house and land packages.We have attached a photo of the current logo and would like to see if it can be improved somehow if needed.We are open to any colours but we have chosen Black and White at this stage. Feel free to change the font and make the logo smarter looking.Play with the colours and see what looks best.We want a card that looks so good know one will want to throw it away!

Target Market(s)

Building profesonals, home buyers

Industry/Entity Type

Building

Contact Information for Business Card

Garrick Tenwood
0275390628
garrickt@hartvale.co.nz

Font styles to use
Serif
Sans Serif

Colors

Designer to choose colors to be used in the design.

Requirements
Must have
• Just the logo on one side and details on the other
• Clean simple looking card
Nice to have
• Round corners and detail like raised or spot UV
• Something that stands out
Should not have
• To title needed, Director etc

```html
<!DOCTYPE html>
<html lang="en">
<head>
<meta charset="utf-8">
<title>Hartvale Business Cards</title>
<link rel="stylesheet" href="https://fonts.googleapis.com/css2?family=Montserrat:wght@400;700&family=Oswald:wght@500&family=Open+Sans:wght@400&display=swap">
<style>
  :root {
    --backdrop: #6a6a6a;
    --card: #13202a;
    --card-deep: #111d26;
    --skyline: #1a2833;
    --brand-blue: #2590d4;
    --text-light: #e9eef2;
  }
  * { box-sizing: border-box; margin: 0; padding: 0; }
  html, body { width: 1200px; height: 1200px; overflow: hidden; }
  body { background: var(--backdrop); position: relative; font-family: "Open Sans", sans-serif; }

  .card {
    position: absolute;
    left: 226px;
    width: 813px;
    height: 464px;
    background: var(--card);
    overflow: hidden;
  }
  .card--details { top: 78px; }
  .card--logo { top: 660px; background: var(--card-deep); }

  .skyline {
    position: absolute;
    left: 0; right: 0; bottom: 0;
    height: 370px;
    background: linear-gradient(180deg, rgba(26,40,51,0) 0%, var(--skyline) 45%, var(--skyline) 100%);
  }

  /* Wordmark */
  .wordmark {
    position: absolute;
    display: flex;
    align-items: center;
    color: var(--brand-blue);
    font-family: "Montserrat", sans-serif;
    font-weight: 700;
    line-height: 1;
  }
  .wordmark__ring {
    border: 3px solid var(--brand-blue);
    border-radius: 50%;
    flex: none;
  }
  .tagline {
    position: absolute;
    color: var(--text-light);
    font-family: "Montserrat", sans-serif;
    font-weight: 400;
    white-space: nowrap;
  }

  /* Front: details */
  .card--details .wordmark { left: 81px; top: 190px; font-size: 44px; gap: 12px; }
  .card--details .wordmark__ring { width: 66px; height: 66px; }
  .card--details .tagline { left: 83px; top: 264px; font-size: 15px; }

  .divider {
    position: absolute;
    left: 406px; top: 161px;
    width: 2px; height: 142px;
    background: var(--brand-blue);
  }
  .person {
    position: absolute;
    left: 426px; top: 152px;
  }
  .person__name {
    font-family: "Oswald", sans-serif;
    font-weight: 500;
    font-size: 41px;
    line-height: 1.1;
    color: var(--brand-blue);
    text-transform: uppercase;
    letter-spacing: 0.2px;
  }
  .person__role {
    font-family: "Montserrat", sans-serif;
    font-size: 19px;
    color: var(--text-light);
    letter-spacing: 0.5px;
    margin-top: -4px;
  }
  .contact {
    list-style: none;
    margin-top: 16px;
  }
  .contact__item {
    display: flex;
    align-items: center;
    gap: 10px;
    font-size: 24px;
    color: var(--text-light);
    height: 36px;
  }
  .contact__icon { width: 20px; height: 20px; flex: none; }

  /* Back: logo */
  .card--logo .wordmark {
    left: 0; right: 0; top: 158px;
    justify-content: center;
    font-size: 90px; gap: 22px;
  }
  .card--logo .wordmark__ring { width: 120px; height: 120px; border-width: 4px; }
  .card--logo .tagline { left: 170px; top: 282px; font-size: 24px; }
</style>
</head>
<body>

  <section class="card card--details">
    <div class="skyline" role="img" aria-label="Faint city skyline silhouette in the background"></div>

    <div class="wordmark">
      <span class="wordmark__name">Hartvale</span>
      <span class="wordmark__ring"></span>
    </div>
    <p class="tagline">Homes inspired by you.</p>

    <div class="divider"></div>

    <div class="person">
      <h1 class="person__name">Garrick Tenwood</h1>
      <p class="person__role">MANAGER</p>
      <ul class="contact">
        <li class="contact__item">
          <svg class="contact__icon" viewBox="0 0 20 20" aria-hidden="true">
            <circle cx="10" cy="10" r="10" fill="var(--brand-blue)"/>
            <path d="M6.4 4.8c.5-.4 1.1-.3 1.4.2l1 1.7c.3.5.2 1-.2 1.3l-.7.5c.5 1.2 1.4 2.2 2.6 2.8l.5-.7c.3-.4.9-.5 1.3-.2l1.7 1c.5.3.6 1 .2 1.4l-.8.9c-.6.6-1.6.7-2.5.3-2.4-1.1-4.3-3-5.4-5.4-.4-.9-.2-1.9.4-2.5z" fill="var(--card)"/>
          </svg>
          <span>027 539 0628</span>
        </li>
        <li class="contact__item">
          <svg class="contact__icon" viewBox="0 0 20 20" aria-hidden="true">
            <circle cx="10" cy="10" r="10" fill="var(--brand-blue)"/>
            <rect x="5" y="6.5" width="10" height="7" rx="0.8" fill="none" stroke="var(--card)" stroke-width="1.3"/>
            <path d="M5.4 7l4.6 3.6L14.6 7" fill="none" stroke="var(--card)" stroke-width="1.3"/>
          </svg>
          <span>garrickt@hartvale.co.nz</span>
        </li>
      </ul>
    </div>
  </section>

  <section class="card card--logo">
    <div class="skyline" role="img" aria-label="Faint city skyline silhouette in the background"></div>
    <div class="wordmark">
      <span class="wordmark__name">Hartvale</span>
      <span class="wordmark__ring"></span>
    </div>
    <p class="tagline">Homes inspired by you.</p>
  </section>

</body>
</html>
```